International Woodworking Brand needs new site

Our Website has not been revamped for a long time.. The imaging and construction are now tired and dated. Its clumsy and cumbersome to edit, uses outdated software. The site can only be edited and updated from NZ. We need multiple editors worldwide refreshing our content, within prescribed templates to maintain look and feel. We want to use a Wordpress platform.

KELBRO is the main brand of the Forvane Industries. Traditionally, the website is branded with KELBRO, the company name. This is incorrect now and needs a shift to our KELBRO brand. Also new levels of service and functionality are required.

KELBRO has a strong reputation in the market place for innovation and leading edge technology in it's field. We have also worked hard to develop a reputation for excellent customer service. Our website also needs to reflect and reinforce these concepts.

We want a fresh, clean, modern site that meets all best practices of SEO marketing, is easy for our customers to navigate and use, and reinforces our brand reputation and our product sales.

See the attached Brief for more specifics.

Target Market(s)

End Users - Woodworkers
Dealers/Stores
KELBRO Employees

More demographic and customer profile info is available on request

Industry/Entity Type

Woodworking

Coding

Coded - Design and coding required

Font styles to use
Sans Serif

Colors
ec1f27

Requirements
Must have
• See the brief attached
Nice to have
• See the brief attached
Should not have
• See the brief attached

```html
<!DOCTYPE html>
<html lang="en">
<head>
<meta charset="utf-8">
<title>KELBRO – Woodworking by Forvane Industries</title>
<link href="https://fonts.googleapis.com/css2?family=Roboto:wght@300;400;500;700&family=Open+Sans:wght@400;600&display=swap" rel="stylesheet">
<style>
:root{
  --red:#ec1f27;
  --dark:#1e1e1e;
  --darker:#141414;
  --grey:#ededed;
  --text:#555;
  --white:#fff;
}
*{box-sizing:border-box;margin:0;padding:0}
html,body{width:1200px;height:2616px;overflow:hidden}
body{font-family:"Open Sans",Arial,sans-serif;color:var(--text);background:var(--white);font-size:14px;line-height:1.6}
h1,h2,h3,h4{font-family:"Roboto",Arial,sans-serif;color:#222}
a{color:inherit;text-decoration:none}

.site-header{height:140px;position:relative}
.brand{position:absolute;left:110px;top:44px;display:flex;align-items:center;gap:10px}
.brand-dot{width:26px;height:26px;border-radius:50%;background:var(--red)}
.brand-name{font-family:"Roboto",sans-serif;font-weight:700;font-size:38px;line-height:1;color:#222;letter-spacing:1px}
.account-links{position:absolute;right:110px;top:56px;display:flex;align-items:center;gap:18px;font-size:12px;color:#666;text-transform:uppercase}
.search-btn{width:26px;height:26px;border-radius:50%;background:#444;display:flex;align-items:center;justify-content:center}

.main-nav{height:52px;background:linear-gradient(#333,#1d1d1d);display:flex;padding:0 110px;justify-content:space-between}
.main-nav a{font-family:"Roboto",sans-serif;font-size:12px;color:#ddd;text-transform:uppercase;line-height:52px;padding:0 22px;font-weight:500}
.main-nav a.active{background:var(--red);color:#fff}

.hero{height:468px;position:relative;background:linear-gradient(120deg,#6b6a68 0%,#8d8b88 35%,#4b4a48 70%,#2c2b2a 100%);text-align:center;color:#fff}
.hero-copy{position:absolute;top:280px;left:0;right:0}
.hero h1{color:#fff;font-size:40px;font-weight:500;letter-spacing:1px;line-height:1.2}
.hero p{font-size:13px;max-width:600px;margin:12px auto 0;color:#eee}
.hero-dots{position:absolute;top:425px;left:50%;transform:translateX(-50%);display:flex;gap:8px}
.hero-dots span{width:10px;height:10px;border-radius:50%;background:rgba(255,255,255,.5)}
.hero-dots span.on{background:var(--red)}
.hero-arrow{position:absolute;top:210px;width:36px;height:36px}
.hero-arrow.prev{left:20px}.hero-arrow.next{right:20px}

.welcome{height:320px;display:flex}
.welcome-text{width:612px;padding:66px 40px 0 110px}
.welcome h2{font-size:26px;font-weight:500;text-transform:uppercase;margin-bottom:18px}
.welcome p{font-size:13px;line-height:1.8}
.read-more{display:inline-flex;align-items:center;gap:8px;margin-top:20px;font-family:"Roboto",sans-serif;font-size:12px;font-weight:700;color:#222;text-transform:uppercase}
.read-more i{width:14px;height:14px;border-radius:50%;background:var(--red);display:inline-block}
.welcome-video{width:548px;background:linear-gradient(135deg,#1f4d7a,#5e8fbd 50%,#173452);position:relative}
.play{position:absolute;left:50%;top:50%;transform:translate(-50%,-50%);text-align:center;color:#fff;font-size:12px;text-transform:uppercase}

.products-bar{height:148px;background:var(--dark);display:flex;align-items:center;justify-content:space-between;padding:0 110px}
.products-bar h2{color:#fff;font-size:30px;font-weight:500;text-transform:uppercase}
.product-tabs{display:flex;gap:4px}
.product-tabs a{font-family:"Roboto",sans-serif;font-size:11px;color:#ddd;text-transform:uppercase;padding:8px 16px;font-weight:500}
.product-tabs a.active{background:var(--red);color:#fff}

.products{height:352px;background:var(--grey);position:relative;padding:32px 100px 0}
.product-grid{display:flex;gap:20px}
.product-card{width:240px;background:#fff;padding:12px;text-align:center;height:280px}
.product-img{height:118px;background:linear-gradient(135deg,#cfd3d6,#9aa3aa)}
.product-card h3{font-size:12px;font-weight:700;text-transform:uppercase;margin:18px 0 8px}
.product-card p{font-size:11px;color:#888;line-height:1.6;padding:0 10px}
.product-card .read-more{margin-top:14px;font-size:11px}
.slide-arrow{position:absolute;top:165px;font-size:22px;color:#555;font-family:"Roboto",sans-serif}
.slide-arrow.prev{left:56px}.slide-arrow.next{right:56px}

.news{height:340px;background:#f4f4f4;padding-top:36px}
.news h2{text-align:center;font-size:28px;font-weight:500;text-transform:uppercase;margin-bottom:40px}
.news-list{display:flex;gap:40px;padding:0 110px}
.news-item{display:flex;gap:26px;width:470px}
.news-img{width:190px;height:130px;flex:none;background:linear-gradient(135deg,#3a3a3a,#8e8e8e)}
.news-img.b{background:linear-gradient(135deg,#2c5a86,#9bb8d2)}
.news-item h3{font-size:16px;font-weight:500;margin-bottom:8px}
.news-item p{font-size:12px;color:#777;line-height:1.7}

.newsletter{height:428px;position:relative;padding:80px 110px 0 440px}
.newsletter-img{position:absolute;left:110px;top:70px;width:290px;height:280px;border-radius:8px;background:linear-gradient(140deg,#eef2f2 0%,#2f7f86 45%,#1f3c40 80%,#f2f2f2 100%)}
.newsletter h2{font-size:28px;font-weight:500;text-transform:uppercase;display:flex;align-items:center;gap:12px}
.newsletter h2 small{font-size:13px;color:#888;text-transform:none;font-weight:400}
.badge{width:80px;height:28px;background:#e0e0e0;border-radius:4px}
.newsletter p{font-size:12px;color:#888;margin:30px 0;max-width:640px;line-height:1.7}
.signup{background:var(--red);padding:14px;display:flex;width:670px}
.signup input{flex:1;height:42px;border:0;padding:0 14px;font-size:12px;font-family:inherit}
.signup button{width:150px;background:var(--darker);color:#fff;border:0;font-family:"Roboto",sans-serif;font-weight:700;text-transform:uppercase;font-size:13px}

.site-footer{height:280px;background:var(--darker);display:flex;padding:34px 110px 0;gap:40px;color:#aaa;font-size:12px}
.site-footer h4{color:#fff;font-size:14px;text-transform:uppercase;font-weight:500;margin-bottom:16px}
.col-connect{width:330px}
.col-links{width:170px}
.col-links li{list-style:none;line-height:2}
.col-contact{flex:1}
.col-contact li{list-style:none;line-height:2.1;display:flex;align-items:center;gap:10px;white-space:nowrap}
.col-contact li i{width:10px;height:10px;flex:none;background:var(--red);border-radius:50%}
.socials{display:flex;gap:10px;margin-top:16px}
.socials span{width:28px;height:28px;border-radius:50%;background:#fff}
.socials span.on{background:var(--red)}

.bottom-bar{height:96px;display:flex;justify-content:space-between;align-items:center;padding:0 110px;font-size:11px;color:#888}
.bottom-brand{font-family:"Roboto",sans-serif;font-weight:700;font-size:30px;color:#555;letter-spacing:1px}
</style>
</head>
<body>

<header class="site-header">
  <a class="brand" href="#"><span class="brand-dot"></span><span class="brand-name">KELBRO</span></a>
  <div class="account-links">
    <span>Register</span><span>|</span><span>Login</span>
    <span class="search-btn"><svg width="12" height="12" viewBox="0 0 12 12"><circle cx="5" cy="5" r="3.5" stroke="#fff" stroke-width="1.5" fill="none"/><line x1="7.6" y1="7.6" x2="11" y2="11" stroke="#fff" stroke-width="1.5"/></svg></span>
  </div>
</header>

<nav class="main-nav">
  <a class="active" href="#">Home</a><a href="#">Products</a><a href="#">Support</a><a href="#">Where to buy</a><a href="#">Register your warranty</a><a href="#">About</a>
</nav>

<section class="hero" role="img" aria-label="Workshop photograph of lathe accessories on a steel bench">
  <svg class="hero-arrow prev" viewBox="0 0 36 36"><polyline points="22,8 12,18 22,28" stroke="#fff" stroke-width="3" fill="none"/></svg>
  <svg class="hero-arrow next" viewBox="0 0 36 36"><polyline points="14,8 24,18 14,28" stroke="#fff" stroke-width="3" fill="none"/></svg>
  <div class="hero-copy">
    <h1>LATHE ACCESSORIES</h1>
    <p>Precision tools built for turners who demand accuracy, durability and a smooth finish on every project, every single day.</p>
  </div>
  <div class="hero-dots"><span></span><span class="on"></span><span></span><span></span></div>
</section>

<section class="welcome">
  <div class="welcome-text">
    <h2>Welcome to KELBRO</h2>
    <p>For over forty years we have designed woodworking machines that combine innovation with dependable engineering. Our lathes, chucks and workshop tools are trusted by hobbyists and professionals around the world, backed by service that keeps you turning.</p>
    <a class="read-more" href="#"><i></i>Read more</a>
  </div>
  <div class="welcome-video" role="img" aria-label="Video still of a chuck mounted on a lathe">
    <div class="play">
      <svg width="70" height="70" viewBox="0 0 70 70"><circle cx="35" cy="35" r="33" fill="rgba(255,255,255,.25)" stroke="#fff" stroke-width="2"/><polygon points="28,22 50,35 28,48" fill="#fff"/></svg>
      <div>Play video</div>
    </div>
  </div>
</section>

<section class="products-bar">
  <h2>Our Products</h2>
  <div class="product-tabs">
    <a class="active" href="#">Lathes</a><a href="#">Lathe accessories</a><a href="#">Chucks</a><a href="#">Chuck accessories</a><a href="#">Workshop</a><a href="#">Store</a>
  </div>
</section>

<section class="products">
  <span class="slide-arrow prev">‹</span><span class="slide-arrow next">›</span>
  <div class="product-grid">
    <article class="product-card"><div class="product-img" role="img" aria-label="Lathe product photo"></div><h3>Suspendisse mauris porta</h3><p>Sturdy cast frame with variable speed for smooth, quiet turning.</p><a class="read-more" href="#"><i></i>View product</a></article>
    <article class="product-card"><div class="product-img" role="img" aria-label="Drill press product photo"></div><h3>Suspendisse mauris porta</h3><p>Sturdy cast frame with variable speed for smooth, quiet turning.</p><a class="read-more" href="#"><i></i>View product</a></article>
    <article class="product-card"><div class="product-img" role="img" aria-label="Chuck product photo"></div><h3>Suspendisse mauris porta</h3><p>Sturdy cast frame with variable speed for smooth, quiet turning.</p><a class="read-more" href="#"><i></i>View product</a></article>
    <article class="product-card"><div class="product-img" role="img" aria-label="Cordless drill product photo"></div><h3>Suspendisse mauris porta</h3><p>Sturdy cast frame with variable speed for smooth, quiet turning.</p><a class="read-more" href="#"><i></i>View product</a></article>
  </div>
</section>

<section class="news">
  <h2>Latest News</h2>
  <div class="news-list">
    <article class="news-item"><div class="news-img" role="img" aria-label="Chuck jaws news photo"></div><div><h3>Lorem ipsum dolor sit amet, conse</h3><p>New jaw sets arrive this season, giving turners a wider grip range and firmer hold on bowls.</p><a class="read-more" href="#"><i></i>Read more</a></div></article>
    <article class="news-item"><div class="news-img b" role="img" aria-label="Drill bit news photo"></div><div><h3>Fusce ultricies efficitur convallis</h3><p>Our dealer network expands across Europe, bringing local service and spare parts closer to you.</p><a class="read-more" href="#"><i></i>Read more</a></div></article>
  </div>
</section>

<section class="newsletter">
  <div class="newsletter-img" role="img" aria-label="Cordless rotary hammer drill"></div>
  <h2>Sign up our newsletter <small>via</small><span class="badge"></span></h2>
  <p>Get product launches, workshop tips and exclusive dealer offers delivered to your inbox each month. We respect your privacy and never share your details with third parties.</p>
  <form class="signup"><input type="email" placeholder="Email Address"><button type="button">Subscribe</button></form>
</section>

<footer class="site-footer">
  <div class="col-connect">
    <h4>Connect us</h4>
    <p>Join our community of turners and makers. Share your projects, ask our team for advice and stay up to date with events near you.</p>
    <div class="socials"><span></span><span></span><span class="on"></span><span></span></div>
  </div>
  <div class="col-links">
    <h4>My account</h4>
    <ul><li>My orders</li><li>My wish list</li><li>My addresses</li><li>My account info</li></ul>
  </div>
  <div class="col-links">
    <h4>Useful links</h4>
    <ul><li>Brands</li><li>Specials</li><li>Help and advice</li><li>Our stores</li><li>Contact us</li></ul>
  </div>
  <div class="col-contact">
    <h4>Contact</h4>
    <ul>
      <li><i></i>48 Kereru Lane, Orewa Bay, NZ</li>
      <li><i></i>+64 9 555 0140</li>
      <li><i></i>+64 9 555 0141</li>
      <li><i></i>hello@forvane-example.com</li>
    </ul>
  </div>
</footer>

<div class="bottom-bar">
  <span>Copyright © 2016 Forvane Industries. All Rights Reserved.</span>
  <span class="bottom-brand">KELBRO</span>
</div>

</body>
</html>
```